Kestrelway Financial Plans

I am looking for a complete resdesign of my small financial presentation. This is a Word Doc/PDF that I print off when meeting with people in private. I often present my "two pager" that I have been using for years and years. It tells them the basics of what I do, how I help people and foundational financial principles.

I have recently gone out on my own in business and have completely rebranded. This presentation is my most used tool, so it is the first of many things I would like to redo. I am hoping it will somehow coordinate with the colors of my business, not necessarily the EXACT same 3 colors everywhere, but have the design colors compliment.

I've uploaded all my logo designs, as well as the current "two-pager". I am not against it going to 3 pages if needed. As it will still land on 2 pages with duplex printing.

It has always been VERY simple. I am wanting it built into a more professional and design specific format, to show off my branding, without being over cluttered.

I am completely open to ANY graphics changes. Obviously some are very novice, the house on the last page has always been overly simplified.

```html
<!DOCTYPE html>
<html lang="en">
<head>
<meta charset="utf-8">
<title>Kestrelway Financial Plans – Presentation</title>
<link href="https://fonts.googleapis.com/css2?family=Oswald:wght@300;400&family=Montserrat:wght@400;500;600;700&display=swap" rel="stylesheet">
<style>
:root{
  --navy:#16203a;
  --green:#1fa846;
  --green-dark:#17913b;
  --gray:#a6a8ab;
  --gray-light:#e6e7e8;
  --bg:#ececec;
  --white:#ffffff;
}
*{margin:0;padding:0;box-sizing:border-box}
html,body{width:1200px;height:633px;overflow:hidden;background:var(--bg);font-family:'Montserrat',sans-serif;color:var(--navy)}
.page{position:absolute;top:78px;width:345px;height:443px;background:var(--white);box-shadow:0 4px 14px rgba(0,0,0,.18);overflow:hidden}
.page--challenge{left:53px}
.page--method{left:429px;width:340px}
.page--rule{left:801px}
.abs{position:absolute}
.brand{position:absolute;left:15px;top:14px;text-align:center}
.brand__name{font-weight:700;font-size:15px;letter-spacing:.3px;color:var(--navy);line-height:1}
.brand__sub{font-weight:700;font-size:5.5px;letter-spacing:1.6px;color:var(--navy);margin-top:3px}
.header-band{position:absolute;right:0;top:0;width:215px;height:50px}
.header-title{position:absolute;right:14px;top:12px;font-family:'Oswald',sans-serif;font-weight:300;font-size:19px;color:var(--white);letter-spacing:.2px}
.pill-title{position:absolute;background:#8f9194;color:var(--white);font-family:'Oswald',sans-serif;font-weight:300;font-size:17px;display:flex;align-items:center;justify-content:center;border-radius:2px}
/* page 1 */
.stat-col{position:absolute;top:78px;width:106px;height:140px}
.stat-col__head{position:relative;height:29px;background:var(--navy);color:var(--white);font-weight:700;font-size:9.5px;display:flex;align-items:flex-end;justify-content:center;padding-bottom:4px;letter-spacing:.3px}
.stat-col__body{height:111px;padding:5px 5px;color:var(--white);font-size:4.6px;line-height:1.28}
.stat-col--gray .stat-col__body{background:var(--gray)}
.stat-col--green .stat-col__body{background:var(--green)}
.stat-col__badge{position:absolute;top:-21px;left:37px;width:32px;height:32px;border-radius:50%;background:var(--green);border:3px solid var(--navy);z-index:1}
.stat{display:flex;gap:3px;margin-bottom:3px}
.stat b{font-weight:700;min-width:13px}
.src{font-style:italic;font-size:4.2px}
.rule{border-top:.5px solid rgba(255,255,255,.6);margin:3px 0}
.step{position:absolute;top:271px;width:60px;text-align:center}
.step__ring{width:60px;height:60px;border-radius:50%;display:flex;align-items:center;justify-content:center}
.step__core{width:36px;height:36px;border-radius:50%;background:var(--white);border:2px solid var(--gray-light)}
.step__label{position:absolute;top:71px;left:-6px;width:72px;font-size:5.3px;font-weight:500;line-height:1.2}
.step__dots{position:absolute;top:95px;left:29px;height:22px;border-left:1.5px dotted var(--navy)}
.step__goal{position:absolute;top:120px;left:-6px;width:72px;font-size:5.3px;font-weight:500;line-height:1.2}
.step__arrow{position:absolute;top:140px;left:25px;color:var(--green);font-size:8px;font-weight:700}
.step__note{position:absolute;top:150px;left:-6px;width:72px;font-size:5.1px;font-weight:500;line-height:1.2}
/* page 2 */
.branch{position:absolute;left:265px;font-size:6.2px;font-weight:500;line-height:1.2}
.partner{position:absolute;width:70px;height:34px;border:1px solid #c9cacc;border-radius:2px;display:flex;align-items:center;justify-content:center}
.partner__mark{width:22px;height:14px;background:var(--gray-light);border-radius:2px}
.pay{position:absolute;left:0;width:100%;text-align:center;font-weight:700;color:var(--green);font-size:13px;top:414px}
/* page 3 */
.rate{position:absolute;top:46px;width:80px}
.rate__head{height:15px;background:var(--green);color:var(--white);font-size:7px;font-weight:700;padding:4px 0 0 8px;position:relative}
.rate__pct{position:absolute;right:4px;top:-6px;width:24px;height:24px;border-radius:50%;background:var(--navy);border:2px solid var(--white);color:var(--green);font-size:8px;font-weight:600;display:flex;align-items:center;justify-content:center}
.rate__body{height:80px;background:var(--gray-light);padding:6px 6px;font-size:5.3px;font-weight:500;line-height:1.6}
.rate__row{display:flex;justify-content:space-between}
.rate__row b{font-weight:700}
.rate__foot{margin-top:8px;text-align:center;font-size:5.4px;line-height:1.3}
.rate__foot b{font-weight:700;display:block}
.pillar{position:absolute;top:278px;width:70px}
.pillar__head{height:15px;background:var(--navy);color:var(--white);font-size:7.5px;font-weight:700;text-align:center;padding-top:3px}
.pillar__body{height:72px;background:var(--gray-light);text-align:center;font-size:5px;line-height:1.3;padding:5px 3px}
.pillar__body p{margin-bottom:5px}
.pillar__tag{height:13px;background:var(--navy);color:var(--green);font-size:6.5px;font-weight:700;text-align:center;padding-top:2px;margin-top:1px}
.band{position:absolute;left:23px;width:302px;height:11px;background:var(--green);color:var(--white);font-size:6.3px;font-weight:700;text-align:center;line-height:11px}
</style>
</head>
<body>

<section class="page page--challenge">
  <div class="brand"><div class="brand__name">KESTRELWAY</div><div class="brand__sub">— FINANCIAL PLANS —</div></div>
  <svg class="header-band" viewBox="0 0 215 50"><polygon points="0,0 215,0 215,50 20,50" fill="var(--green)"/><polygon points="8,0 215,0 215,50 28,50" fill="var(--navy)"/></svg>
  <div class="header-title">THE FINANCIAL CHALLENGE</div>

  <div class="stat-col stat-col--gray" style="left:10px">
    <div class="stat-col__head"><div class="stat-col__badge"></div>SAVINGS</div>
    <div class="stat-col__body">
      <div class="stat"><b>49%</b><span>of Canadian Employees are living paycheque to paycheque.</span></div>
      <div class="stat"><b>25%</b><span>Canadians are unable to cover an unexpected $500 expense.<br><span class="src">National Data Office (Feb 2023)</span></span></div>
      <div class="rule"></div>
      <div class="stat"><b>25%</b><span>of Canadians need to access their retirement savings early.</span></div>
      <div class="stat"><b>20%</b><span>Canadians have no saving</span></div>
      <div class="stat"><b>39%</b><span>of Canadians aged 55-65 have less than $5,000 in savings.<br><span class="src">Federal Data Desk (June 2023)</span></span></div>
    </div>
  </div>
  <div class="stat-col stat-col--green" style="left:119px">
    <div class="stat-col__head"><div class="stat-col__badge" style="border-color:var(--white)"></div>DEBT</div>
    <div class="stat-col__body">
      <p>The average Canadian has $22,131 in consumer debts, which excludes mortgages.<br><span class="src">Ledgerline (Aug 2024)</span></p><br>
      <p>Over 55% of Canadians hold credit card debt and the total Canadian household debt has increased to $2.52 trillion, including consumer credit, mortgage and non-mortgage loans.<br><span class="src">Lenders Council (Aug 2024)</span></p>
    </div>
  </div>
  <div class="stat-col stat-col--gray" style="left:228px">
    <div class="stat-col__head"><div class="stat-col__badge"></div>INSURANCE</div>
    <div class="stat-col__body">
      <div class="stat"><b>49%</b><span>of Canadians do not have individual life insurance coverage, but</span></div>
      <div class="stat"><b>48%</b><span>say their families would face financial trouble within 6 months of losing someone.<br><span class="src">Insura Research (Apr 2023)</span></span></div>
      <div class="rule"></div>
      <p>2-in-5 Canadians (43% Women / 44% Men) will be diagnosed with a form of cancer or other critical illness during their lifetime. Every 7 seconds.<br><span class="src">Wellness Data Hub (June 2024)</span></p>
    </div>
  </div>

  <div class="pill-title" style="left:84px;top:232px;width:169px;height:30px">FACING THE CHALLENGE</div>

  <div class="step" style="left:11px"><div class="step__ring" style="background:var(--navy)"><div class="step__core"></div></div>
    <div class="step__label" style="top:75px">CASH FLOW</div><div class="step__dots"></div><div class="step__goal">ANALYZE</div><div class="step__arrow">↓</div><div class="step__note">Free Up<br>$400-$600</div></div>
  <div class="step" style="left:63px"><div class="step__ring" style="background:var(--green)"><div class="step__core"></div></div>
    <div class="step__label">CASH FLOW<br>PROTECTION</div><div class="step__dots"></div><div class="step__goal" style="top:116px">INCOME<br>PROTECTION</div><div class="step__arrow">↓</div><div class="step__note">Life Insurance<br>CI/DI Insurance</div></div>
  <div class="step" style="left:116px"><div class="step__ring" style="background:var(--gray)"><div class="step__core"></div></div>
    <div class="step__label">DEBT<br>MANAGEMENT</div><div class="step__dots"></div><div class="step__goal">20%</div><div class="step__arrow">↓</div><div class="step__note">6-7%</div></div>
  <div class="step" style="left:169px"><div class="step__ring" style="background:var(--navy)"><div class="step__core"></div></div>
    <div class="step__label">EMERGENCY<br>FUND</div><div class="step__dots"></div><div class="step__goal">IF / WHEN</div><div class="step__arrow">↓</div><div class="step__note">3-6 Months</div></div>
  <div class="step" style="left:222px"><div class="step__ring" style="background:var(--green)"><div class="step__core"></div></div>
    <div class="step__label">BUILD<br>WEALTH</div><div class="step__dots"></div><div class="step__goal" style="top:114px">FINANCIAL<br>INDEPENDENCE<br>NUMBER (FIN)</div></div>
  <div class="step" style="left:274px"><div class="step__ring" style="background:var(--gray)"><div class="step__core"></div></div>
    <div class="step__label">PRESERVE<br>WEALTH</div><div class="step__dots"></div><div class="step__goal" style="top:116px">LEAVING<br>A LEGACY</div><div class="step__arrow">↓</div><div class="step__note">Will Prep</div></div>
</section>

<section class="page page--method">
  <div class="brand"><div class="brand__name">KESTRELWAY</div><div class="brand__sub">— FINANCIAL PLANS —</div></div>
  <svg class="header-band" viewBox="0 0 215 50"><polygon points="0,0 215,0 215,50 20,50" fill="var(--green)"/><polygon points="8,0 215,0 215,50 28,50" fill="var(--navy)"/></svg>
  <div class="header-title" style="right:24px">HOW AM I DOING IT</div>

  <svg class="abs" style="left:0;top:0" width="340" height="280" viewBox="0 0 340 280">
    <circle cx="133" cy="161" r="104" fill="var(--gray-light)"/>
    <path d="M133 161 L133 64 A97 97 0 0 0 133 258 Z" fill="var(--green)"/>
    <path d="M133 161 L133 64 A97 97 0 0 1 230 161 Z" fill="var(--navy)"/>
    <path d="M133 161 L230 161 A97 97 0 0 1 133 258 Z" fill="var(--gray)"/>
    <circle cx="133" cy="161" r="35" fill="var(--white)" stroke="var(--gray-light)" stroke-width="3"/>
    <rect x="177" y="97" width="14" height="16" fill="none" stroke="var(--green)" stroke-width="1.2"/>
    <rect x="58" y="128" width="22" height="13" rx="2" fill="none" stroke="var(--white)" stroke-width="1.4"/>
    <rect x="169" y="203" width="22" height="13" rx="2" fill="none" stroke="var(--navy)" stroke-width="1.4"/>
    <text x="178" y="132" text-anchor="middle" font-family="Montserrat" font-weight="700" font-size="9.5" fill="var(--green)">TAXES</text>
    <text x="69" y="157" text-anchor="middle" font-family="Montserrat" font-weight="700" font-size="9" fill="var(--white)">LIVING</text>
    <text x="69" y="169" text-anchor="middle" font-family="Montserrat" font-weight="700" font-size="9" fill="var(--white)">EXPENSES</text>
    <text x="133" y="174" text-anchor="middle" font-family="Montserrat" font-weight="700" font-size="9" fill="var(--navy)">SAVINGS</text>
    <text x="180" y="228" text-anchor="middle" font-family="Montserrat" font-weight="700" font-size="9" fill="var(--navy)">DEBT</text>
    <path d="M133 140 q-9 0 -9 8 q0 7 9 7 q9 0 9 -7 q0 -8 -9 -8z" fill="var(--navy)"/>
    <path d="M258 87 H240 V240 H258 M240 135 H258 M240 189 H258" fill="none" stroke="var(--gray)" stroke-width="1"/>
  </svg>
  <div class="branch" style="top:82px">RETIREMENT<br>SAVINGS</div>
  <div class="branch" style="top:130px">CHILDREN'S<br>EDUCATION</div>
  <div class="branch" style="top:185px">PROPER<br>PROTECTION</div>
  <div class="branch" style="top:234px">FREEDOM<br>FROM DEBT</div>

  <div class="partner" style="left:57px;top:279px"><div class="partner__mark"></div></div>
  <div class="partner" style="left:132px;top:279px"><div class="partner__mark"></div></div>
  <div class="partner" style="left:207px;top:279px"><div class="partner__mark"></div></div>
  <div class="partner" style="left:23px;top:319px"><div class="partner__mark"></div></div>
  <div class="partner" style="left:98px;top:319px"><div class="partner__mark"></div></div>
  <div class="partner" style="left:173px;top:319px"><div class="partner__mark"></div></div>
  <div class="partner" style="left:248px;top:319px"><div class="partner__mark"></div></div>
  <div class="partner" style="left:63px;top:358px"><div class="partner__mark"></div></div>
  <div class="partner" style="left:138px;top:358px"><div class="partner__mark"></div></div>
  <div class="partner" style="left:213px;top:358px"><div class="partner__mark"></div></div>

  <svg class="abs" style="left:163px;top:396px" width="14" height="14" viewBox="0 0 14 14"><path d="M5 0h4v7h4l-6 7-6-7h4z" fill="var(--navy)"/></svg>
  <div class="pay">PAY US</div>
</section>

<section class="page page--rule">
  <div class="brand" style="top:10px"><div class="brand__name">KESTRELWAY</div><div class="brand__sub">— FINANCIAL PLANS —</div></div>
  <svg class="header-band" style="height:34px;width:195px" viewBox="0 0 195 34"><polygon points="0,0 195,0 195,34 22,34" fill="var(--green)"/><polygon points="8,0 195,0 195,34 30,34" fill="var(--navy)"/></svg>
  <div class="header-title" style="top:4px;right:55px;font-size:18px">RULE OF 72</div>

  <div class="rate" style="left:11px"><div class="rate__head">AGE<span class="rate__pct">4%</span></div>
    <div class="rate__body"><div class="rate__row"><b>29</b><span>$10,000</span></div><div class="rate__row"><b>47</b><span>$20,000</span></div><div class="rate__row"><b>65</b><span>$40,000</span></div></div>
    <div class="rate__foot">Money Doubles<b>EVERY 18 YEARS</b></div></div>
  <div class="rate" style="left:93px"><div class="rate__head">AGE<span class="rate__pct">6%</span></div>
    <div class="rate__body"><div class="rate__row"><b>29</b><span>$10,000</span></div><div class="rate__row"><b>41</b><span>$20,000</span></div><div class="rate__row"><b>53</b><span>$40,000</span></div><div class="rate__row"><b>65</b><span>$80,000</span></div></div>
    <div class="rate__foot">Money Doubles<b>EVERY 12 YEARS</b></div></div>
  <div class="rate" style="left:175px"><div class="rate__head">AGE<span class="rate__pct">8%</span></div>
    <div class="rate__body"><div class="rate__row"><b>29</b><span>$10,000</span></div><div class="rate__row"><b>38</b><span>$20,000</span></div><div class="rate__row"><b>47</b><span>$40,000</span></div><div class="rate__row"><b>56</b><span>$80,000</span></div><div class="rate__row"><b>65</b><span>$160,000</span></div></div>
    <div class="rate__foot">Money Doubles<b>EVERY 9 YEARS</b></div></div>
  <div class="rate" style="left:257px"><div class="rate__head">AGE<span class="rate__pct">12%</span></div>
    <div class="rate__body" style="line-height:1.5"><div class="rate__row"><b>29</b><span>$10,000</span></div><div class="rate__row"><b>35</b><span>$20,000</span></div><div class="rate__row"><b>41</b><span>$40,000</span></div><div class="rate__row"><b>47</b><span>$80,000</span></div><div class="rate__row"><b>53</b><span>$160,000</span></div><div class="rate__row"><b>59</b><span>$320,000</span></div><div class="rate__row"><b>65</b><span>$640,000</span></div></div>
    <div class="rate__foot">Money Doubles<b>EVERY 6 YEARS</b></div></div>

  <div class="pill-title" style="left:118px;top:172px;width:100px;height:29px">STRUCTURE</div>

  <svg class="abs" style="left:0;top:205px" width="345" height="75" viewBox="0 0 345 75">
    <polygon points="172,4 328,67 16,67" fill="var(--navy)"/>
    <rect x="16" y="69" width="314" height="4" fill="var(--green)"/>
    <circle cx="172" cy="12" r="5" fill="var(--green)"/>
    <path d="M150 50 Q170 48 172 20 Q174 48 194 50" fill="none" stroke="var(--white)" stroke-width=".8"/>
    <text x="172" y="63" text-anchor="middle" font-family="Oswald" font-weight="300" font-size="14" fill="var(--white)">WEALTH BUILDING</text>
  </svg>

  <div class="pillar" style="left:18px"><div class="pillar__head">HOME</div><div class="pillar__body"><p>Partner with Mortgage Brokers for Best Rates</p><p>Mortgage Insurance Alternatives</p></div><div class="pillar__tag">SELL</div></div>
  <div class="pillar" style="left:99px"><div class="pillar__head">RRSP</div><div class="pillar__body"><p>Tax Deduction</p><p>Tax Deferred</p></div><div class="pillar__tag">100% TAX</div></div>
  <div class="pillar" style="left:180px"><div class="pillar__head">TFSA</div><div class="pillar__body"><p>No Tax Deduction</p><p>Tax Free Growth</p><p>2009 - $95,000</p><p>Limit 2023<br>$7,000/Yr</p></div><div class="pillar__tag">0% TAX</div></div>
  <div class="pillar" style="left:258px"><div class="pillar__head">PERM LIFE</div><div class="pillar__body"><p>No Tax Deduction</p><p>Qualify</p><p>Tax Deferred Growth</p></div><div class="pillar__tag">0% TAX</div></div>

  <div class="band" style="top:382px">EMERGENCY/ OPPORTUNITY FUNDING</div>
  <div class="band" style="top:395px">DEBT MANAGEMENT</div>
  <div class="band" style="top:408px">CASHFLOW PROTECTION (LIFE INS/CI/DI)</div>
  <div class="band" style="top:421px">CASHFLOW</div>
  <div class="abs" style="left:291px;top:389px;width:30px;height:30px;border-radius:50%;background:var(--white);border:1px solid var(--gray-light)"></div>
</section>

</body>
</html>
```